Corvane Capital Business Cards

These are professional business cards that are for my family office.
Put fake emails and phone numbers as of now until I finalize those components. This family office controls my families investments, assets, and future. The cards should be professional.
..
.
.
.
I just uploaded another variation of a logo I would like to see as a business card to I am inbeteen which logo to use

Target Market(s)

business

Industry/Entity Type

business

Contact Information for Business Card

Professional, wealth related, finance related.

Requirements
Must have
• Logo

```html
<!DOCTYPE html>
<html lang="en">
<head>
<meta charset="utf-8">
<title>Corvane Capital Business Cards</title>
<link rel="stylesheet" href="https://fonts.googleapis.com/css2?family=Cinzel:wght@600&family=Montserrat:wght@400;700&display=swap">
<style>
  :root {
    --backdrop: #ebebeb;
    --card: #ffffff;
    --ink: #191c28;
    --ink-soft: #2b2e38;
    --placeholder: #e4e4e7;
  }
  * { margin: 0; padding: 0; box-sizing: border-box; }
  html, body {
    width: 1200px;
    height: 716px;
    overflow: hidden;
    background: var(--backdrop);
  }
  .sheet { position: relative; width: 1200px; height: 716px; }
  .card {
    position: absolute;
    left: 369px;
    width: 461px;
    height: 263px;
    background: var(--card);
    border-radius: 12px;
  }
  .card--front { top: 94px; }
  .card--back { top: 385px; }

  .brand-dot {
    position: absolute;
    width: 96px;
    height: 96px;
    border-radius: 50%;
    background: var(--placeholder);
  }
  .card--front .brand-dot { left: 183px; top: 62px; }
  .card--back .brand-dot { left: 81px; top: 78px; }

  .brand-name {
    position: absolute;
    font-family: "Cinzel", serif;
    font-weight: 600;
    color: var(--ink);
    white-space: nowrap;
    line-height: 1;
  }
  .card--front .brand-name {
    left: 0; right: 0; top: 193px;
    text-align: center;
    font-size: 26px;
  }
  .card--back .brand-name {
    left: 236px; top: 66px;
    font-size: 19px;
  }

  .divider {
    position: absolute;
    left: 222px; top: 66px;
    width: 1.5px; height: 126px;
    background: var(--ink);
  }

  .contact {
    position: absolute;
    left: 235px;
    font-family: "Montserrat", sans-serif;
    color: var(--ink);
    white-space: nowrap;
    line-height: 1;
  }
  .contact__name { top: 115px; font-size: 18px; font-weight: 700; letter-spacing: -0.2px; }
  .contact__role { top: 134px; font-size: 13px; color: var(--ink-soft); }
  .contact__line {
    display: flex;
    align-items: center;
    gap: 6px;
    font-size: 12.5px;
    color: var(--ink-soft);
  }
  .contact__line--phone { top: 160px; }
  .contact__line--email { top: 177px; }
  .contact__icon { width: 11px; height: 10px; fill: var(--ink); flex: none; }
</style>
</head>
<body>
<main class="sheet">
  <section class="card card--front" aria-label="Card front">
    <div class="brand-dot" role="img" aria-label="Logo area"></div>
    <p class="brand-name">Corvane Capital</p>
  </section>

  <section class="card card--back" aria-label="Card back">
    <div class="brand-dot" role="img" aria-label="Logo area"></div>
    <div class="divider"></div>
    <p class="brand-name">Corvane Capital</p>
    <p class="contact contact__name">DANIEL REYES</p>
    <p class="contact contact__role">Founder</p>
    <p class="contact contact__line contact__line--phone">
      <svg class="contact__icon" viewBox="0 0 12 10" aria-hidden="true">
        <path d="M0 3.2C1.5 0.6 10.5 0.6 12 3.2L10.6 4.4 8.6 3.6V2.6C7 2 5 2 3.4 2.6V3.6L1.4 4.4Z"/>
        <path d="M2.6 5.2 4 3.8H8L9.4 5.2 10 9.6H2Z"/>
      </svg>
      555-014-2280
    </p>
    <p class="contact contact__line contact__line--email">
      <svg class="contact__icon" viewBox="0 0 12 10" aria-hidden="true">
        <path d="M0 1H12V1.6L6 5.6 0 1.6Z"/>
        <path d="M0 2.8 6 6.8 12 2.8V9H0Z"/>
      </svg>
      info@corvanecapital.com
    </p>
  </section>
</main>
</body>
</html>
```